Strategy and Technology Consulting - Our Story and Values Page

Interior Page design – Our History and Our Values

Our homepage has been designed and we are looking for a design for one of the interior pages. This interior page tells the story of Our History and Our Values

Because the homepage has been designed, we would like this interior page to reflect the design of the homepage without being a mirror image of the homepage.

This site will be implemented in WordPress using the Elementor framework.

Font: Poppins medium and Poppins dark
Illustrations: Our homepage illustrations were designed by “Brelin 1974” on Quillmark. Compatible original or stock illustrations are welcome. Stock photography is also welcome. Brelin is also available through Brelin Tosamek on Ravolo

Uploaded Files
• Homepage design – this is the design we will use for our homepage. Contest entries should reflect this basic style but should be distinctly different from the homepage.
• Our History and Our Values – Wireframe – the basic layout of the page we are looking for.
• Our History and Our Values – Word document with the text supporting the wireframe.
• Color Palette – please use colors compatible with the palette attached.

Our Story - timeline
There is a timeline element in the wireframe. The wireframe displays this as a series of chevrons (arrows), but it does not need to be. Creativity in display of the timeline is appreciated.

Our Values
If you look at the Word document, you will see that there are a lot of words on the page. The winning design will present the information in a way that engages the user without overwhelming them with too much to read. For example, they may click on a value and see more information.

Target Market(s)

CIO's and Technology Executives

Number of Pages Required

1 page

Font styles to use
Sans Serif
Other font styles liked:
• Poppin

Requirements
Must have
• A timeline element, all of our values
Nice to have
• Clever timeline display

```html
<!DOCTYPE html>
<html lang="en">
<head>
<meta charset="UTF-8">
<title>Veltrano – Our Story and Values</title>
<link rel="stylesheet" href="https://fonts.googleapis.com/css2?family=Poppins:wght@400;500;600;700;800&display=swap">
<style>
:root{
  --gold:#eeb11c;
  --gold-dark:#d99a0a;
  --blue:#0b4a8c;
  --blue-deep:#0a3a70;
  --navy:#14305a;
  --ink:#1c1f26;
  --text:#3a3f4a;
  --muted:#6b7280;
  --card:#ffffff;
  --paper:#f4f5f7;
  --footer-top:#6d7480;
  --footer-bottom:#3b414b;
}
*{box-sizing:border-box;margin:0;padding:0}
html,body{width:1200px;height:5048px;overflow:hidden}
body{font-family:"Poppins",sans-serif;color:var(--ink);background:#fff;position:relative}
.abs{position:absolute}

/* header */
.site-header{position:absolute;left:0;top:0;width:1200px;height:80px;background:#fff;box-shadow:0 2px 10px rgba(0,0,0,.05)}
.brand{position:absolute;display:flex;align-items:center;gap:10px;font-weight:600;color:var(--blue-deep)}
.brand-dot{width:14px;height:14px;border-radius:50%;background:var(--gold)}
.site-header .brand{left:40px;top:18px;font-size:34px}
.main-nav{position:absolute;left:530px;top:28px;display:flex;gap:26px;font-size:14px;font-weight:500;color:var(--ink)}
.main-nav span::after{content:" ▾";font-size:10px}
.main-nav span.plain::after{content:""}
.btn-contact{position:absolute;background:var(--gold);color:#fff;font-weight:700;font-size:14px;border-radius:24px;text-align:center;letter-spacing:.5px}
.site-header .btn-contact{left:980px;top:18px;width:130px;height:44px;line-height:44px}

/* story */
.section-title{position:absolute;left:0;width:1200px;text-align:center;font-size:38px;font-weight:700;letter-spacing:1px}
.story-title{top:150px;color:var(--ink)}
.timeline-card{position:absolute;background:var(--paper);border-radius:18px;overflow:hidden;box-shadow:0 6px 18px rgba(0,0,0,.08)}
.timeline-card .period{height:84px;background:var(--gold);color:#fff;font-size:30px;font-weight:700;text-align:center;line-height:84px}
.timeline-card ul{list-style:none;padding:30px 36px;font-size:19px;line-height:34px;color:var(--text)}
.card-early{left:88px;top:300px;width:330px;height:400px}
.card-late{left:790px;top:300px;width:320px;height:400px}
.card-mid{left:408px;top:262px;width:392px;height:470px;background:#fff;z-index:2;box-shadow:0 14px 34px rgba(10,40,90,.22);border:2px solid #e2e6ee}
.card-mid .period{background:var(--blue-deep);height:90px;line-height:90px}
.card-mid ul{font-size:20px}

/* values band */
.values-band{position:absolute;left:0;top:830px;width:1200px;height:3560px;background:var(--blue)}
.values-title{top:925px;color:#fff}
.value-card{position:absolute;left:150px;width:940px;background:var(--card);border-radius:22px;box-shadow:0 10px 30px rgba(0,0,0,.2)}
.value-card.text-right{padding:48px 56px 40px 400px}
.value-card.text-left{padding:48px 400px 40px 56px}
.value-card h3{font-size:22px;font-weight:700;margin-bottom:16px;color:var(--ink)}
.value-card p{font-size:17px;line-height:31px;color:var(--text)}
.value-art{position:absolute;width:390px;height:380px;border-radius:22px;background:#fff;padding:26px;box-shadow:0 10px 30px rgba(0,0,0,.2);z-index:2}
.value-art .art{width:100%;height:100%;border-radius:14px}
.art-people{background:linear-gradient(135deg,#dce8f7,#f6d9a0)}
.art-puzzle{background:linear-gradient(135deg,#c9ddf2,#f1c5a0)}
.art-desk{background:linear-gradient(135deg,#e9edf3,#f4d08a)}
.art-stairs{background:linear-gradient(135deg,#dbe6f4,#9fbde3)}
.art-target{background:linear-gradient(135deg,#e7edf6,#f0b49a)}
.art-bulb{background:linear-gradient(135deg,#e3ecf8,#f7de8c)}
.art-help{background:linear-gradient(135deg,#f6dcae,#a8c6ea)}

/* newsletter */
.newsletter{position:absolute;left:128px;top:4190px;width:944px;height:190px;background:var(--gold);border-radius:95px;z-index:3}
.newsletter h2{position:absolute;left:80px;top:42px;font-size:34px;font-weight:700;color:#fff}
.newsletter p{position:absolute;left:80px;top:98px;width:380px;font-size:14px;line-height:20px;color:#fff;font-weight:500}
.subscribe-field{position:absolute;left:520px;top:64px;width:360px;height:60px;background:#fff;border-radius:30px}
.subscribe-field span{position:absolute;left:56px;top:18px;font-size:14px;color:var(--muted)}
.subscribe-field .mail-dot{position:absolute;left:26px;top:24px;width:12px;height:12px;border-radius:50%;border:2px solid var(--gold)}
.subscribe-go{position:absolute;right:8px;top:8px;width:44px;height:44px;border-radius:50%;background:var(--gold)}

/* footer */
.site-footer{position:absolute;left:0;top:4390px;width:1200px;height:658px;background:linear-gradient(160deg,var(--footer-top),var(--footer-bottom))}
.site-footer .brand{left:120px;top:210px;font-size:54px;color:#fff;font-weight:500}
.site-footer .brand-dot{width:18px;height:18px}
.socials{position:absolute;left:180px;top:308px;display:flex;gap:14px}
.socials i{width:36px;height:36px;border-radius:50%;background:rgba(255,255,255,.3);display:block}
.site-footer .btn-contact{left:210px;top:370px;width:120px;height:38px;line-height:38px;font-size:13px}
.footer-col{position:absolute;top:160px;color:#fff}
.footer-col h4{font-size:22px;font-weight:700;margin-bottom:22px}
.footer-col ul{list-style:none;font-size:14px;line-height:30px}
.footer-col li::before{content:"› ";color:var(--gold)}
.col-links{left:490px}
.col-services{left:670px}
.col-contact{left:905px}
.contact-item{display:flex;gap:10px;font-size:14px;line-height:22px;margin-bottom:16px}
.contact-item .ico{width:20px;height:20px;flex:none;margin-top:2px}
.contact-item b{display:block;color:var(--gold);font-weight:600}
.copyright{position:absolute;left:0;top:530px;width:1200px;height:128px;background:var(--blue-deep);color:#fff;font-size:15px;text-align:center;line-height:70px}
.chat-bubble{position:absolute;left:1140px;top:4970px;width:46px;height:46px;border-radius:50%;background:var(--gold);z-index:4}
</style>
</head>
<body>

<header class="site-header">
  <div class="brand"><span class="brand-dot"></span>Veltrano</div>
  <nav class="main-nav">
    <span class="plain">US</span><span>ABOUT US</span><span>SERVICES</span><span>INSIGHTS</span><span>JOIN US</span>
  </nav>
  <div class="btn-contact">CONTACT US</div>
</header>

<h1 class="section-title story-title">OUR STORY</h1>

<div class="timeline-card card-early">
  <div class="period">2017 – 2019</div>
  <ul>
    <li>Growth Strategy Focus</li>
    <li>Consistent, Modest Growth</li>
    <li>Preliminary Focus on Technology</li>
    <li>Eureka! Implementing strategy is hard.</li>
  </ul>
</div>
<div class="timeline-card card-mid">
  <div class="period">2020 – 2021</div>
  <ul>
    <li>Pandemic Pauses Growth</li>
    <li>Rethinking :</li>
    <li>– the business model</li>
    <li>– the delivery model</li>
  </ul>
</div>
<div class="timeline-card card-late">
  <div class="period">2022 &amp; ONWARD</div>
  <ul>
    <li>Leadership Team for Focus on Essential Areas</li>
    <li>Rapid Growth</li>
    <li>Customer Success</li>
  </ul>
</div>

<section class="values-band"></section>
<h2 class="section-title values-title">OUR VALUES</h2>

<!-- value 1 -->
<div class="value-art" style="left:120px;top:1080px"><div class="art art-people" role="img" aria-label="Illustration of a diverse team standing together with growth charts"></div></div>
<div class="value-card text-right" style="top:1060px;height:360px">
  <h3>THE VALUE OF EVERY HUMAN. REGARDLESS.</h3>
  <p>Each person's unique experiences and perspectives add vibrant hues to the tapestry of our shared existence. In a world where diversity paints the canvas of humanity, true beauty is found in recognizing the inherent and incalculable value of every human being.</p>
</div>

<!-- value 2 -->
<div class="value-art" style="left:690px;top:1500px"><div class="art art-puzzle" role="img" aria-label="Illustration of colleagues fitting puzzle pieces together"></div></div>
<div class="value-card text-left" style="top:1540px;height:340px">
  <h3>COLLABORATION</h3>
  <p>Collaboration in work transforms individual endeavors into symphonies of collective achievement. Through collaboration, diverse talents converge, fostering a rich exchange of ideas that amplifies creativity, accelerates progress, and brings forth solutions beyond what a single mind could conceive.</p>
</div>

<!-- value 3 -->
<div class="value-art" style="left:120px;top:1960px"><div class="art art-desk" role="img" aria-label="Illustration of a person working on a laptop surrounded by ideas and gears"></div></div>
<div class="value-card text-right" style="top:1990px;height:340px;padding-top:80px">
  <h3>PASSION</h3>
  <p>Passion infuses our work with energy, transforming routine tasks into opportunities for creativity and innovation. Fueled by passion, individuals become unstoppable forces, driven to overcome challenges and achieve remarkable outcomes that benefit them and inspire those around them.</p>
</div>

<!-- value 4 -->
<div class="value-art" style="left:690px;top:2430px"><div class="art art-stairs" role="img" aria-label="Illustration of people climbing steps toward a flag"></div></div>
<div class="value-card text-left" style="top:2480px;height:330px">
  <h3>EXCELLENCE</h3>
  <p>Excellence isn't a destination; it's a continuous journey of refinement and growth. Striving for excellence cultivates a culture of continuous improvement, fostering innovation, credibility, and a lasting impact that resonates far beyond the immediate task.</p>
</div>

<!-- value 5 -->
<div class="value-art" style="left:120px;top:2900px"><div class="art art-target" role="img" aria-label="Illustration of a person running up bars toward a target"></div></div>
<div class="value-card text-right" style="top:2940px;height:300px;padding-top:60px">
  <h3>TENACITY</h3>
  <p>Tenacity is the unwavering anchor that keeps us grounded amidst adversity, propelling us forward when faced with obstacles. The resilience to persist, adapt, and learn from setbacks leads to the mastery of skills and the fulfillment of ambitious goals.</p>
</div>

<!-- value 6 -->
<div class="value-art" style="left:690px;top:3360px"><div class="art art-bulb" role="img" aria-label="Illustration of people around a glowing light bulb idea"></div></div>
<div class="value-card text-left" style="top:3400px;height:320px">
  <h3>SOLUTION MINDSET</h3>
  <p>A solution mindset is the compass that directs our focus from problems to possibilities. It empowers us to navigate challenges with a proactive mindset, igniting a journey of exploration and innovation that not only resolves issues but also paves the way for continuous growth and success.</p>
</div>

<!-- value 7 -->
<div class="value-art" style="left:120px;top:3830px"><div class="art art-help" role="img" aria-label="Illustration of people helping each other climb blocks"></div></div>
<div class="value-card text-right" style="top:3820px;height:310px;padding-top:56px">
  <h3>GENEROSITY</h3>
  <p>Generosity creates a virtuous cycle of goodwill, fostering a sense of unity and shared purpose among colleagues. By freely sharing knowledge, support, and resources, we uplift those around us and contribute to a collaborative environment where collective achievements flourish.</p>
</div>

<footer class="site-footer">
  <div class="brand"><span class="brand-dot"></span>Veltrano</div>
  <div class="socials"><i></i><i></i><i></i><i></i></div>
  <div class="btn-contact">CONTACT US</div>

  <div class="footer-col col-links">
    <h4>Quick links</h4>
    <ul><li>Home</li><li>About Us</li><li>Services</li><li>Insights</li><li>Join Us</li><li>Contact Us</li></ul>
  </div>
  <div class="footer-col col-services">
    <h4>Our Services</h4>
    <ul><li>Business Transformation</li><li>ERP Implementations</li><li>ERP Solutions</li><li>AI Solutions</li><li>Building the Right Teams</li></ul>
  </div>
  <div class="footer-col col-contact">
    <h4>Contact Info</h4>
    <div class="contact-item">
      <svg class="ico" viewBox="0 0 20 20"><rect x="2" y="4" width="16" height="12" rx="2" fill="none" stroke="#eeb11c" stroke-width="2"/><path d="M2 5l8 6 8-6" fill="none" stroke="#eeb11c" stroke-width="2"/></svg>
      <div><b>Email</b>hello@veltrano.com</div>
    </div>
    <div class="contact-item">
      <svg class="ico" viewBox="0 0 20 20"><path d="M5 2l3 4-2 2c1 2 3 4 5 5l2-2 4 3-2 3C9 17 3 11 2 4z" fill="#eeb11c"/></svg>
      <div><b>Phone</b>+44 20 7946 0321</div>
    </div>
    <div class="contact-item">
      <svg class="ico" viewBox="0 0 20 20"><path d="M10 1a6 6 0 016 6c0 5-6 12-6 12S4 12 4 7a6 6 0 016-6z" fill="#eeb11c"/><circle cx="10" cy="7" r="2.2" fill="#4a505a"/></svg>
      <div><b>Location</b>Some address line goes<br>here city name</div>
    </div>
  </div>

  <div class="copyright">© Veltrano Design 2023. All Rights Reserved</div>
</footer>

<div class="newsletter">
  <h2>Subscribe Our Newsletter</h2>
  <p>Subscribe our newsletter to receive the latest news and exclusive offers every week. No spam.</p>
  <div class="subscribe-field">
    <span class="mail-dot"></span>
    <span>Enter email address</span>
    <svg class="subscribe-go" viewBox="0 0 44 44"><circle cx="22" cy="22" r="22" fill="#eeb11c"/><path d="M15 22h13M23 16l6 6-6 6" fill="none" stroke="#fff" stroke-width="3" stroke-linecap="round" stroke-linejoin="round"/></svg>
  </div>
</div>

<div class="chat-bubble"></div>

</body>
</html>
```